Business card for a Exhibition booth fabrication company

Hi. My company would like to change our corporate name card. We are an events and Exhibition stand builder company. We would like our corporate name card to resonate what we do. I need someone to create something unique that relates to the industry that I am in. The graphic designer should be creative to incorporate the elements of my industry and try to blend in well in the design of the card. Our aim is to ensure that we are unique and our card can look different from our competitors.
Updates

Target Market(s)

Marketing and events manager from all companies

Contact Information for Business Card

The business card should have the following details:
Name
Job Title
Email
Website

Colors

Designer to choose colors to be used in the design.

Requirements
Must have
• The card must be look something that is relevant to the service that I am providing. My website is: www.velmora-buildworks.com
• You can see my website to get more information on what service that I am doing
Nice to have
• On the back of my card, I would like to have a globe image with the incorporation of my company logo. This is to indicate that my services can be done in any part of the world.

```html
<!DOCTYPE html>
<html lang="en">
<head>
<meta charset="utf-8">
<title>Velmora Buildworks – Business Card</title>
<link rel="stylesheet" href="https://fonts.googleapis.com/css2?family=Lato:wght@400;700&display=swap">
<style>
  :root {
    --stage: #222222;
    --paper: #fbfbfb;
    --ink: #2b2b2b;
    --brand-red: #e3232b;
    --band-black: #1b1b1b;
    --back-base: #1e1e1e;
    --globe-light: #9a9a9a;
    --globe-dark: #2a2a2a;
    --rule: #444444;
  }
  * { box-sizing: border-box; margin: 0; padding: 0; }
  html, body {
    width: 980px; height: 1200px; overflow: hidden;
    background: var(--stage);
    font-family: "Lato", sans-serif;
  }
  .canvas { position: relative; width: 980px; height: 1200px; }
  .card {
    position: absolute; left: 126px; width: 756px; height: 432px; overflow: hidden;
  }
  .card-front { top: 101px; background: var(--paper); }
  .card-back { top: 642px; background: var(--back-base); }

  .brand-wordmark {
    position: absolute; left: 0; width: 413px; top: 252px; text-align: center;
    font-weight: 700; font-size: 21px; letter-spacing: 2px; color: var(--ink);
  }
  .divider {
    position: absolute; left: 413px; top: 120px; width: 1.5px; height: 187px; background: var(--rule);
  }
  .contact-block { position: absolute; left: 438px; top: 112px; color: var(--ink); }
  .person-name { font-size: 32px; font-weight: 400; color: var(--brand-red); line-height: 1.1; }
  .person-title { font-size: 17px; letter-spacing: 0.5px; margin-top: 1px; }
  .contact-list { list-style: none; margin-top: 27px; }
  .contact-list li {
    display: flex; align-items: center; font-size: 17px; letter-spacing: 0.6px;
    height: 30px;
  }
  .contact-list svg { width: 14px; height: 14px; margin-right: 12px; fill: var(--brand-red); flex: none; }

  .edge-band { position: absolute; left: 0; bottom: 0; width: 756px; height: 19px; }

  .globe {
    position: absolute; left: 189px; top: 26px; width: 378px; height: 378px; border-radius: 50%;
    background: radial-gradient(circle at 68% 62%, var(--globe-light) 0%, #5c5c5c 40%, var(--globe-dark) 80%);
  }
  .back-wordmark {
    position: absolute; left: 189px; width: 378px; top: 179px; text-align: center;
    font-weight: 700; font-size: 30px; line-height: 36px; letter-spacing: 3px; color: var(--brand-red);
  }
  .back-wordmark span { display: block; }
</style>
</head>
<body>
<div class="canvas">
  <section class="card card-front">
    <div class="brand-wordmark">VELMORA BUILDWORKS</div>
    <div class="divider"></div>
    <div class="contact-block">
      <h1 class="person-name">Adrian Keller</h1>
      <p class="person-title">Founder &amp; CEO</p>
      <ul class="contact-list">
        <li><svg viewBox="0 0 16 16"><path d="M3.6 1.2l2.3 2.6-1.3 1.8c.9 2 2.5 3.6 4.6 4.6l1.8-1.3 2.6 2.3-1.2 2.3C7 13.5 2.5 9 1.4 2.4z"/></svg>+65 81042276 (Singapore)</li>
        <li><svg viewBox="0 0 16 16"><path d="M3.6 1.2l2.3 2.6-1.3 1.8c.9 2 2.5 3.6 4.6 4.6l1.8-1.3 2.6 2.3-1.2 2.3C7 13.5 2.5 9 1.4 2.4z"/></svg>+974 55213048 (Qatar)</li>
        <li><svg viewBox="0 0 16 16"><path d="M1 3h14v1.5L8 9 1 4.5z M1 6.3l7 4.5 7-4.5V13H1z"/></svg>info@velmora-buildworks.com</li>
        <li><svg viewBox="0 0 16 16"><path fill="none" stroke="#e3232b" stroke-width="1.2" d="M8 1.5a6.5 6.5 0 1 0 0 13a6.5 6.5 0 1 0 0-13zM1.5 8h13M8 1.5c-3 3.5-3 9.5 0 13M8 1.5c3 3.5 3 9.5 0 13M2.6 4.7h10.8M2.6 11.3h10.8"/></svg>www.velmora-buildworks.com</li>
      </ul>
    </div>
    <svg class="edge-band" viewBox="0 0 756 19" preserveAspectRatio="none">
      <polygon points="0,0 382,0 364,19 0,19" fill="#e3232b"/>
      <polygon points="382,0 390,0 372,19 364,19" fill="#ffffff"/>
      <polygon points="390,0 756,0 756,19 372,19" fill="#1b1b1b"/>
    </svg>
  </section>

  <section class="card card-back">
    <div class="globe" role="img" aria-label="Grey world globe illustration showing the continents"></div>
    <div class="back-wordmark"><span>VELMORA</span><span>BUILDWORKS</span></div>
  </section>
</div>
</body>
</html>
```